Menu Cards - Bar & Restaurant

We're a casual college sports bar in Madison, WI. We're looking for simple & creative design for menu cards that are double sided. The first card is to identify our wing sauces on the front side with our tap list on the back. The second card is for our taco night and again our tap list on the back. The font used in our logo is Air Conditioner, but I don't want this to be limiting.
Target Market(s)
18-25 college kids
Industry/Entity Type
College

```html
<!DOCTYPE html>
<html lang="en">
<head>
<meta charset="utf-8">
<title>Rounders Bar &amp; Grille – Taco Night</title>
<link rel="stylesheet" href="https://fonts.googleapis.com/css2?family=Fredericka+the+Great&family=Forum&family=Questrial&display=swap">
<style>
  :root {
    --board: #2a2c2f;
    --board-light: #3a3d41;
    --chalk: #ecebe8;
    --brand-red: #e8262b;
    --panel: #ecebea;
    --ink: #262626;
    --rule: #6b6b6b;
    --taco-gold: #d9a03a;
    --taco-brown: #8a5a2e;
  }
  * { margin: 0; padding: 0; box-sizing: border-box; }
  html, body { width: 1200px; height: 929px; overflow: hidden; background: var(--board); }
  .menu-card {
    position: relative;
    width: 1200px;
    height: 929px;
    background: linear-gradient(90deg, var(--board) 0%, var(--board-light) 50%, var(--board) 100%);
    font-family: "Questrial", sans-serif;
  }
  .venue-name {
    position: absolute;
    left: 80px;
    top: 66px;
    font-family: "Questrial", sans-serif;
    font-size: 34px;
    line-height: 40px;
    color: var(--chalk);
    white-space: nowrap;
  }
  .title {
    position: absolute;
    left: 557px;
    top: 38px;
    width: 536px;
    font-family: "Fredericka the Great", cursive;
    font-weight: 400;
    font-size: 78px;
    line-height: 84px;
    color: var(--chalk);
    letter-spacing: 2px;
    text-align: center;
    white-space: nowrap;
  }
  .frame {
    position: absolute;
    left: 64px;
    top: 153px;
    width: 1069px;
    height: 709px;
    border: 8px solid var(--brand-red);
    border-radius: 46px;
    background: var(--panel);
    overflow: hidden;
  }
  .food-photo {
    position: absolute;
    left: 0;
    top: 0;
    width: 450px;
    height: 100%;
    background: radial-gradient(ellipse at 45% 55%, var(--taco-gold) 0%, #c98a2c 45%, var(--taco-brown) 100%);
  }
  .price-list {
    position: absolute;
    left: 522px;
    top: 190px;
    width: 603px;
    list-style: none;
    text-align: center;
  }
  .price-group { padding-bottom: 12px; }
  .price-group + .price-group::before {
    content: "";
    display: block;
    width: 426px;
    margin: 0 auto 10px;
    border-top: 1.5px dotted var(--rule);
  }
  .item {
    display: block;
    font-size: 33px;
    line-height: 43px;
    color: var(--brand-red);
  }
  .price {
    display: block;
    font-family: "Forum", serif;
    font-size: 44px;
    line-height: 52px;
    color: var(--ink);
  }
</style>
</head>
<body>
  <main class="menu-card">
    <p class="venue-name">Rounders bar &amp; grille</p>
    <h1 class="title">TACO NIGHT</h1>

    <section class="frame">
      <div class="food-photo" role="img" aria-label="Photo of crunchy beef hard shell tacos topped with lettuce, diced tomato and shredded cheese"></div>
    </section>

    <ul class="price-list">
      <li class="price-group">
        <span class="item">Beef hard shell</span>
        <span class="price">$0.50</span>
      </li>
      <li class="price-group">
        <span class="item">Beef soft shell</span>
        <span class="item">Chicken hard shell</span>
        <span class="price">$1</span>
      </li>
      <li class="price-group">
        <span class="item">Chicken soft shell</span>
        <span class="price">$1.50</span>
      </li>
      <li class="price-group">
        <span class="item">Chips &amp; Salsa</span>
        <span class="price">$2</span>
      </li>
      <li class="price-group">
        <span class="item">Chicken, Steak, or Cheese</span>
        <span class="item">Chimichonga</span>
        <span class="price">$5</span>
      </li>
    </ul>
  </main>
</body>
</html>
```